"Harbor Builders" is a residential building company and needs a new business card design and may re

We would like a redesign based on the existing logo, and would like to see a new font as well. We are bespoke home builders who build sustainable energy efficient homes.

Industry/Entity Type

Construction

Contact Information for Business Card

Business card size 40mm x 90mm

Colors

Designer to choose colors to be used in the design.

```html
<!DOCTYPE html>
<html lang="en">
<head>
<meta charset="utf-8">
<title>Harbor Builders – Business Card</title>
<link href="https://fonts.googleapis.com/css2?family=Source+Sans+3:wght@400;600;700&display=swap" rel="stylesheet">
<style>
  :root {
    --backdrop: #8e8f8f;
    --paper: #e4e4e4;
    --ink: #060708;
    --green: #a3b72d;
    --light-text: #d6d6d6;
    --white: #ffffff;
  }
  * { box-sizing: border-box; margin: 0; padding: 0; }
  html, body { width: 1105px; height: 1200px; overflow: hidden; }
  body {
    background: var(--backdrop);
    font-family: "Source Sans 3", "Myriad Pro", Arial, sans-serif;
    position: relative;
  }
  .card {
    position: absolute;
    left: 182px;
    width: 748px;
    height: 427px;
    overflow: hidden;
  }
  .card--front { top: 119px; background: var(--paper); }
  .card--back { top: 636px; background: var(--green); }

  .front-bands { position: absolute; inset: 0; }

  .brand {
    position: absolute;
    left: 59px;
    top: 52px;
    display: flex;
    align-items: center;
    gap: 16px;
  }
  .brand__mark {
    width: 44px;
    height: 44px;
    background: var(--green);
  }
  .brand__name {
    font-size: 44px;
    font-weight: 600;
    color: var(--ink);
    line-height: 1;
    letter-spacing: -0.5px;
  }

  .holder-name {
    position: absolute;
    left: 59px;
    top: 178px;
    font-size: 26px;
    font-weight: 700;
    color: var(--ink);
  }

  .company-details {
    position: absolute;
    right: 36px;
    top: 200px;
    text-align: right;
    font-size: 16.5px;
    line-height: 23.3px;
    color: var(--light-text);
  }
  .company-details strong { font-weight: 700; }

  .contact-list {
    position: absolute;
    right: 36px;
    top: 326px;
    list-style: none;
    font-size: 16.5px;
    line-height: 23.5px;
    color: var(--light-text);
    text-align: right;
  }
  .contact-list li {
    display: flex;
    justify-content: flex-end;
    align-items: center;
    gap: 10px;
  }
  .contact-list svg { width: 15px; height: 15px; flex: none; }

  .back-name {
    position: absolute;
    left: 0; right: 0;
    top: 190px;
    text-align: center;
    font-size: 58px;
    font-weight: 600;
    color: var(--ink);
    letter-spacing: -0.5px;
  }
  .back-web {
    position: absolute;
    left: 0; right: 0;
    top: 354px;
    text-align: center;
    font-size: 17.5px;
    font-weight: 700;
    letter-spacing: 3.6px;
    color: var(--ink);
  }
</style>
</head>
<body>

  <section class="card card--front">
    <svg class="front-bands" viewBox="0 0 748 427" width="748" height="427" aria-hidden="true">
      <polygon points="0,225 205,325 748,63 748,427 0,427" fill="var(--green)"/>
      <polygon points="0,233 205,333 748,71 748,427 0,427" fill="var(--white)"/>
      <polygon points="0,237 205,337 748,75 748,427 0,427" fill="var(--ink)"/>
    </svg>

    <div class="brand">
      <span class="brand__mark"></span>
      <span class="brand__name">harbor builders</span>
    </div>

    <h1 class="holder-name">Daniel Ferraro</h1>

    <div class="company-details">
      <p><strong>Registration:</strong> 40387</p>
      <p><strong>ABN:</strong> 52 904 316 778</p>
      <p><strong>Harbor Builders Pty Ltd</strong></p>
      <p>PO Box 2140 Bayside</p>
      <p>LPO Northport WA 6210</p>
    </div>

    <ul class="contact-list">
      <li>0417 285 930
        <svg viewBox="0 0 15 15" aria-hidden="true"><rect x="3.5" y="0.8" width="8" height="13.4" rx="1.4" fill="none" stroke="var(--green)" stroke-width="1.6"/><rect x="5.5" y="11" width="4" height="1.3" fill="var(--green)"/></svg>
      </li>
      <li>daniel@harborbuilders.com.au
        <svg viewBox="0 0 15 15" aria-hidden="true"><rect x="1" y="3" width="13" height="9" fill="var(--green)"/><polyline points="1,3 7.5,8 14,3" fill="none" stroke="var(--ink)" stroke-width="1.2"/></svg>
      </li>
      <li>www.harborbuilders.com.au
        <svg viewBox="0 0 15 15" aria-hidden="true"><circle cx="7.5" cy="7.5" r="6.5" fill="var(--green)"/><ellipse cx="7.5" cy="7.5" rx="2.6" ry="6.5" fill="none" stroke="var(--ink)" stroke-width="1"/><line x1="1" y1="7.5" x2="14" y2="7.5" stroke="var(--ink)" stroke-width="1"/></svg>
      </li>
    </ul>
  </section>

  <section class="card card--back">
    <p class="back-name">harbor builders</p>
    <p class="back-web">WWW.HARBORBUILDERS.COM.AU</p>
  </section>

</body>
</html>
```